Moravel Aesthetic Doctor

I require an elegant, luxurious looking business card for my aesthetic business. I am a doctor and that will set me aside from competitors. I am planning to provide home and spa based treatments to clients with high expectations. I have attached my logo.

```html
<!DOCTYPE html>
<html lang="en">
<head>
<meta charset="utf-8">
<title>Moravel Aesthetic Doctor — Business Card</title>
<link href="https://fonts.googleapis.com/css2?family=Montserrat:wght@300;400;500;600&display=swap" rel="stylesheet">
<style>
  :root {
    --stage: #1c1c1d;
    --card-dark: #3b3c3e;
    --card-light: #ffffff;
    --brand-blue: #1ba2e2;
    --soft-blue: #8fd3f4;
    --steel: #5d5e61;
    --ink: #2f3033;
    --mist: #e9eaec;
  }
  * { margin: 0; padding: 0; box-sizing: border-box; }
  html, body { width: 1200px; height: 930px; overflow: hidden; }
  body {
    background: var(--stage);
    font-family: "Montserrat", sans-serif;
    position: relative;
  }
  .card {
    position: absolute;
    width: 580px;
    height: 340px;
    border-radius: 22px;
    overflow: hidden;
    box-shadow: 0 18px 40px rgba(0,0,0,.55);
  }

  /* Front */
  .card--front {
    left: 90px; top: 100px;
    background: var(--card-dark);
    color: var(--mist);
  }
  .brand {
    display: flex; align-items: center; gap: 16px;
  }
  .brand__dot {
    width: 54px; height: 54px; border-radius: 50%;
    border: 2px solid currentColor; flex: none;
  }
  .brand__name {
    font-weight: 300; letter-spacing: .12em; line-height: 1.15;
  }
  .brand__name span { display: block; }
  .brand__name .word { font-size: 40px; }
  .brand__name .role { font-size: 15px; letter-spacing: .2em; }
  .card--front .brand {
    position: absolute; left: 110px; top: 70px;
    color: var(--soft-blue);
  }
  .services {
    position: absolute; left: 0; right: 0; top: 200px;
    text-align: center; font-size: 15px; line-height: 1.75;
    letter-spacing: .03em;
  }
  .services .sep { color: var(--brand-blue); padding: 0 6px; }
  .services .tagline { text-transform: uppercase; letter-spacing: .06em; }

  /* Back */
  .card--back {
    left: 530px; top: 480px;
    background: var(--card-light);
    color: var(--ink);
  }
  .card--back .brand {
    position: absolute; left: 34px; top: 40px;
    color: var(--brand-blue);
  }
  .card--back .brand__dot { width: 42px; height: 42px; }
  .card--back .brand__name .word { font-size: 28px; }
  .card--back .brand__name .role { font-size: 11px; }
  .doctor {
    position: absolute; right: 34px; top: 44px; text-align: right;
  }
  .doctor__name {
    color: var(--brand-blue); font-weight: 600; font-size: 17px;
  }
  .doctor__title { font-size: 12.5px; line-height: 1.4; margin-top: 4px; }
  .rule {
    position: absolute; height: 1px; background: var(--brand-blue);
  }
  .rule--name { right: 34px; top: 116px; width: 250px; }
  .rule--contact { left: 34px; top: 200px; width: 300px; }
  .contact {
    position: absolute; left: 34px; top: 212px;
    list-style: none; font-size: 14px; line-height: 1.55;
  }
  .contact li { display: flex; align-items: center; gap: 9px; }
  .contact svg { width: 12px; height: 12px; flex: none; }
  .card__band { position: absolute; left: 0; bottom: 0; width: 100%; height: 110px; }
</style>
</head>
<body>

  <section class="card card--front" aria-label="Card front">
    <div class="brand">
      <span class="brand__dot"></span>
      <div class="brand__name"><span class="word">MORAVEL</span><span class="role">AESTHETIC DOCTOR</span></div>
    </div>
    <p class="services">
      Dermal injectables<span class="sep">|</span>Plasma facials<span class="sep">|</span>Microneedling<br>
      Skin boosters<span class="sep">|</span>Excessive sweating<br>
      <span class="tagline">Home and spa based treatments</span>
    </p>
  </section>

  <section class="card card--back" aria-label="Card back">
    <div class="brand">
      <span class="brand__dot"></span>
      <div class="brand__name"><span class="word">MORAVEL</span><span class="role">AESTHETIC DOCTOR</span></div>
    </div>

    <div class="doctor">
      <p class="doctor__name">Dr Elena Varsk MRCPCH MD</p>
      <p class="doctor__title">Australasian Diploma<br>of Aesthetic Medicine</p>
    </div>
    <div class="rule rule--name"></div>
    <div class="rule rule--contact"></div>

    <ul class="contact">
      <li><svg viewBox="0 0 12 12"><path d="M2.5 1h2l1 2.5-1.3 1a6 6 0 0 0 3.3 3.3l1-1.3 2.5 1v2c0 .6-.4 1-1 1A9 9 0 0 1 1.5 2c0-.6.4-1 1-1z" fill="#1ba2e2"/></svg>0800 474 118</li>
      <li><svg viewBox="0 0 12 12"><rect x="1" y="2.5" width="10" height="7" rx="1" fill="none" stroke="#1ba2e2" stroke-width="1.3"/><path d="M1.5 3l4.5 3.5L10.5 3" fill="none" stroke="#1ba2e2" stroke-width="1.3"/></svg>elena@moravel.co.nz</li>
      <li><svg viewBox="0 0 12 12"><circle cx="6" cy="6" r="4.8" fill="none" stroke="#1ba2e2" stroke-width="1.2"/><path d="M1.2 6h9.6M6 1.2c-2.4 2.6-2.4 7 0 9.6M6 1.2c2.4 2.6 2.4 7 0 9.6" fill="none" stroke="#1ba2e2" stroke-width="1"/></svg>www.moravel.co.nz</li>
    </ul>

    <svg class="card__band" viewBox="0 0 580 110" preserveAspectRatio="none" aria-hidden="true">
      <path d="M0 96 L360 96 C400 96 410 40 450 34 L580 30 L580 110 L0 110 Z" fill="#5d5e61"/>
      <path d="M0 88 L352 88 C392 88 402 44 440 40 L450 40 C412 48 404 100 360 100 L0 100 Z" fill="#1ba2e2"/>
      <path d="M0 92 L356 92 C396 92 406 44 446 37" fill="none" stroke="#ffffff" stroke-width="3"/>
    </svg>
  </section>

</body>
</html>
```